KVR - Redesign (PSD Files Only)

Requirements for the site:

1. We need our logo recreated, please use the same design and change colors to work on a white background

2. The site is a "Wizard" based site, that takes the customer through the process of creating a unique web presence that suits there needs

3.Colors Needed - Main "Dark Blue" Secondary = "Dark Grey" -Other = "Light Grey and White"

4.We need a CRISP CLEAN DESIGN, simple design

5.Wireframes are a general layout and may be modified by you to enhance the design

6. We want a complete web 5.0 look with big buttons and text boxes

7.The more personality the better

8. Current Site brightpolehub.example

9.See attachments for wireframes

10. Designer should deliver PSD files, no coding is required

11. The portfolio wireframe, should look like the design of the artflockly portfolio template
Updates

KEEP IT SIMPLE.,.....

We like the quillmark scaffold style of designs

```html
<!DOCTYPE html>
<html lang="en">
<head>
<meta charset="utf-8">
<title>KVR – Custom Website Design</title>
<link href="https://fonts.googleapis.com/css2?family=Open+Sans:wght@400;600;700;800&display=swap" rel="stylesheet">
<style>
:root{
  --navy:#0b2447;
  --navy-deep:#061833;
  --blue:#1b5ea8;
  --blue-bright:#2b7fd4;
  --grey-dark:#2b2b2b;
  --grey-mid:#8a8f96;
  --grey-light:#d9dadc;
  --white:#ffffff;
  --black:#111214;
  --orange:#f7941d;
  --text:#444a52;
}
*{box-sizing:border-box;margin:0;padding:0}
html,body{width:710px;height:1200px;overflow:hidden}
body{font-family:"Open Sans",Arial,sans-serif;background:var(--grey-light);position:relative;color:var(--text)}
.page{position:relative;width:710px;height:1200px}

/* hero */
.hero{position:absolute;left:0;top:0;width:710px;height:286px;
  background:radial-gradient(ellipse at 50% 55%,#1d5596 0%,#0f3566 45%,var(--navy-deep) 100%)}
.nav{position:absolute;left:108px;top:0;display:flex}
.nav a{display:block;padding:4px 8px;font-size:9px;font-weight:600;color:var(--white);text-decoration:none}
.nav a.is-active{background:var(--blue-bright)}
.phone{position:absolute;right:108px;top:3px;font-size:11px;font-weight:700;color:var(--white);display:flex;align-items:center;gap:4px}
.headline{position:absolute;left:0;width:710px;top:38px;text-align:center;color:var(--white);font-size:21px;font-weight:800}
.subline{position:absolute;left:180px;width:350px;top:70px;text-align:center;color:#c7d6ea;font-size:8px;line-height:11px}
.bubble{position:absolute;border-radius:50%;background:radial-gradient(circle at 40% 35%,#1c2f4a,#060d18);
  border:1px solid #3d5f8a;color:var(--white);font-size:8px;font-weight:600;text-align:center;
  display:flex;align-items:center;justify-content:center;line-height:10px;padding:6px}
.logo-ring{position:absolute;left:303px;top:128px;width:104px;height:104px;border-radius:50%;
  background:radial-gradient(circle,#1f62ac,#0b2e5a);border:2px solid #4f86c6;display:flex;align-items:center;justify-content:center}
.logo-disc{width:70px;height:70px;border-radius:50%;background:var(--white);display:flex;align-items:center;justify-content:center;
  font-size:22px;font-weight:800;color:var(--navy)}
.step{position:absolute;left:0;width:710px;top:238px;text-align:center;color:var(--white);font-size:10px;font-weight:600;letter-spacing:1px}

/* project bar */
.project{position:absolute;left:140px;top:288px;width:430px;height:30px;display:flex}
.project-input{flex:1;background:var(--white);border:1px solid #c6c9cd;font-size:9px;color:#9aa0a6;padding:9px 10px}
.project-btn{width:128px;background:var(--navy);color:var(--white);font-size:11px;font-weight:700;display:flex;align-items:center;justify-content:center}

/* services */
.services{position:absolute;left:111px;top:340px;width:488px;height:294px;background:var(--white);display:flex;box-shadow:0 1px 3px rgba(0,0,0,.15)}
.service{flex:1;padding:12px 8px 0 10px;border-right:1px solid #e4e5e7;position:relative}
.service:last-child{border-right:none}
.service-icon{height:30px;color:var(--navy)}
.service h3{font-size:9px;font-weight:700;color:var(--navy);margin-top:6px}
.service .lead{font-size:6.5px;line-height:9px;color:var(--grey-dark);font-weight:600;margin-top:3px}
.service ul{list-style:none;margin-top:6px}
.service li{font-size:6px;line-height:10px;color:var(--grey-mid)}
.service li::before{content:"› ";color:var(--blue)}
.learn{position:absolute;left:10px;bottom:12px;display:flex;align-items:center;gap:4px;font-size:6.5px;color:var(--grey-mid)}
.learn span{width:14px;height:14px;border-radius:50%;border:1px solid var(--orange);color:var(--orange);display:flex;align-items:center;justify-content:center;font-size:8px}

/* portfolio */
.portfolio{position:absolute;left:0;top:675px;width:710px;height:378px;background:var(--black)}
.tile{position:absolute;background:var(--white);padding:3px}
.tile-art{width:100%;height:calc(100% - 18px)}
.tile-cap{height:15px;background:#1e1f22;color:var(--white);font-size:7px;padding:3px 5px;margin-top:3px}
.dots{position:absolute;left:343px;top:360px;display:flex;gap:4px}
.dots i{width:5px;height:5px;border-radius:50%;background:#555}
.dots i.on{background:#bbb}

/* footer */
.footer{position:absolute;left:0;top:1053px;width:710px;height:147px;background:var(--navy-deep)}
.foot-nav{position:absolute;left:111px;top:48px;font-size:7px;color:#c9d3e0}
.foot-copy{position:absolute;left:111px;top:60px;font-size:6px;color:#8b99ad}
.partner{position:absolute;left:111px;top:76px;width:70px;height:24px;background:var(--white);border-radius:2px}
.social{position:absolute;left:306px;top:42px;display:flex;gap:5px}
.social i{width:14px;height:14px;border-radius:50%;background:var(--white)}
.foot-phone{position:absolute;left:306px;top:62px;font-size:11px;font-weight:700;color:var(--white)}
.consult{position:absolute;left:475px;top:42px;width:124px;height:24px;background:var(--orange);color:var(--white);font-size:10px;font-weight:700;display:flex;align-items:center;justify-content:center;border-radius:2px}
</style>
</head>
<body>
<div class="page">

  <header class="hero">
    <nav class="nav">
      <a href="#">Home</a><a href="#" class="is-active">About Us</a><a href="#">Portfolio</a><a href="#">Contact Us</a>
    </nav>
    <div class="phone">
      <svg width="10" height="10" viewBox="0 0 24 24"><path fill="#fff" d="M6.6 10.8a15 15 0 0 0 6.6 6.6l2.2-2.2a1 1 0 0 1 1-.25 11.4 11.4 0 0 0 3.6.57 1 1 0 0 1 1 1V20a1 1 0 0 1-1 1A17 17 0 0 1 3 4a1 1 0 0 1 1-1h3.5a1 1 0 0 1 1 1c0 1.25.2 2.45.57 3.57a1 1 0 0 1-.25 1z"/></svg>
      1800-555-0142
    </div>
    <h1 class="headline">Get a Custome Website Design in 21 Days or LESS !</h1>
    <p class="subline">Find out why we're the #1 custom website design marketplace. Our network of designers will create 50+ web design samples for you to choose and our marketing experts will pave the way your success.</p>

    <div class="bubble" style="left:145px;top:137px;width:66px;height:66px">24x7<br>customer<br>support</div>
    <div class="bubble" style="left:204px;top:197px;width:66px;height:66px">100% No<br>Obligation<br>Free Web<br>Quote</div>
    <div class="logo-ring"><div class="logo-disc">KVR</div></div>
    <div class="bubble" style="left:433px;top:197px;width:66px;height:66px">Save<br>100% on<br>Webdesign</div>
    <div class="bubble" style="left:507px;top:137px;width:66px;height:66px">100%<br>Moneyback<br>Guarantee</div>
    <div class="step">STEP 1</div>
  </header>

  <form class="project">
    <div class="project-input">Name you project</div>
    <div class="project-btn">Get Started Now</div>
  </form>

  <section class="services">
    <article class="service">
      <svg class="service-icon" width="30" height="30" viewBox="0 0 30 30"><rect x="3" y="5" width="24" height="20" fill="none" stroke="currentColor" stroke-width="2"/><path d="M8 15l5 5 9-10" stroke="currentColor" stroke-width="2.5" fill="none"/></svg>
      <h3>Why Choose KVR ?</h3>
      <p class="lead">We are a full service design &amp; marketing company that will handle everything</p>
      <ul><li>Dedicated Project Manager</li><li>Single Point of Contact</li><li>Marketing Coaches</li><li>Live Chat</li><li>On Design Options for you to choose</li></ul>
      <div class="learn"><span>›</span>Learn More</div>
    </article>
    <article class="service">
      <svg class="service-icon" width="30" height="30" viewBox="0 0 30 30"><circle cx="15" cy="15" r="11" fill="none" stroke="currentColor" stroke-width="2"/><path d="M4 15h22M15 4c-5 6-5 16 0 22M15 4c5 6 5 16 0 22" stroke="currentColor" stroke-width="1.5" fill="none"/></svg>
      <h3>Web Services</h3>
      <p class="lead">We specialize in the following design services</p>
      <ul><li>Web Design</li><li>E-commerce Design</li><li>Web Programming</li><li>Logo Design</li><li>Stationary / Print Design</li><li>UX Design</li><li>Email Template Design</li></ul>
      <div class="learn"><span>›</span>Learn More</div>
    </article>
    <article class="service">
      <svg class="service-icon" width="30" height="30" viewBox="0 0 30 30"><path d="M3 26h24" stroke="currentColor" stroke-width="2"/><rect x="6" y="16" width="4" height="10" fill="currentColor"/><rect x="13" y="10" width="4" height="16" fill="currentColor"/><rect x="20" y="5" width="4" height="21" fill="currentColor"/></svg>
      <h3>Makeing Services</h3>
      <p class="lead">We handle all online marketing including the following</p>
      <ul><li>Paid Search Ads</li><li>Local Listing Marketing</li><li>Search Engine Optimization</li><li>Email Marketing</li><li>Social Media Marketing</li></ul>
      <div class="learn"><span>›</span>Learn More</div>
    </article>
    <article class="service">
      <svg class="service-icon" width="30" height="30" viewBox="0 0 30 30"><circle cx="15" cy="15" r="6" fill="none" stroke="currentColor" stroke-width="3"/><path d="M15 3v5M15 22v5M3 15h5M22 15h5M6.5 6.5l3.5 3.5M20 20l3.5 3.5M6.5 23.5l3.5-3.5M20 10l3.5-3.5" stroke="currentColor" stroke-width="3"/></svg>
      <h3>Maintanence Services</h3>
      <p class="lead">Let us maintain your site and save up to 50% on the following</p>
      <ul><li>Website Hosting</li><li>Software Upgrades</li><li>Custom Web Programming</li><li>Website Marketing</li></ul>
      <div class="learn"><span>›</span>Learn More</div>
    </article>
  </section>

  <section class="portfolio">
    <div class="tile" style="left:114px;top:40px;width:151px;height:112px">
      <div class="tile-art" role="img" aria-label="Screenshot of a dark website design with red header" style="background:linear-gradient(#5a2a2a,#2d2f35)"></div>
      <div class="tile-cap">Lorem Ipsum Title...</div>
    </div>
    <div class="tile" style="left:279px;top:40px;width:147px;height:170px">
      <div class="tile-art" role="img" aria-label="Screenshot of a light website design with product grid" style="background:linear-gradient(#f1ede6,#c9c2b6)"></div>
      <div class="tile-cap">Lorem Ipsum Title...</div>
    </div>
    <div class="tile" style="left:443px;top:40px;width:154px;height:112px">
      <div class="tile-art" role="img" aria-label="Screenshot of a blue and red retail website design" style="background:linear-gradient(#dbe6f4,#c2343a)"></div>
      <div class="tile-cap">Lorem Ipsum Title...</div>
    </div>
    <div class="tile" style="left:114px;top:165px;width:151px;height:128px">
      <div class="tile-art" role="img" aria-label="Printed t-shirt design" style="background:linear-gradient(#f4f4f4,#2e2e2e)"></div>
      <div class="tile-cap">Lorem Ipsum Title...</div>
    </div>
    <div class="tile" style="left:443px;top:177px;width:154px;height:107px">
      <div class="tile-art" role="img" aria-label="Colourful cartoon lettering artwork" style="background:linear-gradient(#fbe9e0,#e2547a)"></div>
      <div class="tile-cap">Lorem Ipsum Title...</div>
    </div>
    <div class="tile" style="left:279px;top:224px;width:147px;height:107px">
      <div class="tile-art" role="img" aria-label="Orange cook-off event artwork" style="background:linear-gradient(#f6c46a,#d9642a)"></div>
      <div class="tile-cap">Lorem Ipsum Title...</div>
    </div>
    <div class="dots"><i class="on"></i><i></i><i></i></div>
  </section>

  <footer class="footer">
    <div class="foot-nav">Home &nbsp;|&nbsp; About Us &nbsp;|&nbsp; Portfolio &nbsp;|&nbsp; Contact Us</div>
    <div class="foot-copy">Copyright © 2014 KVR Studios Inc. - All Rights Reserved</div>
    <div class="partner" role="img" aria-label="Partner badge"></div>
    <div class="social"><i></i><i></i><i></i><i></i><i></i></div>
    <div class="foot-phone">1800-555-0142</div>
    <div class="consult">Request Consultant</div>
  </footer>

</div>
</body>
</html>
```